5 website banners (slides show)

We need 5 website sliding banners created for a website all about internet safety. The topics for each banner are:

Cyberbullying
Fraud
seniors
social networking

Sizes: 953 pixels x 281 pixels

I have stock images to use or feel free to use your own or one I can purchase from pixelharbor.example.

Industry/Entity Type

Internet

```html
<!DOCTYPE html>
<html lang="en">
<head>
<meta charset="utf-8">
<title>Cyberbullying – Internet Safety Banner</title>
<link rel="stylesheet" href="https://fonts.googleapis.com/css2?family=Open+Sans:wght@400&display=swap">
<style>
  :root {
    --canvas: #ffffff;
    --title-gold: #b0924c;
    --body-grey: #555555;
    --wall-blue: #bfe2ea;
    --shirt-teal: #3f7d96;
    --skin-warm: #b88866;
    --floor-light: #ece7e1;
  }
  html, body {
    margin: 0;
    padding: 0;
    width: 1200px;
    height: 354px;
    overflow: hidden;
    background: var(--canvas);
  }
  .banner {
    position: relative;
    width: 1200px;
    height: 354px;
    background: var(--canvas);
    font-family: "Open Sans", Arial, sans-serif;
    overflow: hidden;
  }
  .banner__photo {
    position: absolute;
    left: 0;
    top: 0;
    width: 620px;
    height: 354px;
    background:
      linear-gradient(90deg, rgba(255,255,255,0) 0%, rgba(255,255,255,0) 55%, #ffffff 100%),
      linear-gradient(180deg, var(--wall-blue) 0%, rgba(191,226,234,0) 45%),
      linear-gradient(90deg, var(--shirt-teal) 0%, #5f8ea2 22%, var(--skin-warm) 45%, #d9a07e 62%, var(--floor-light) 80%, #ffffff 100%);
  }
  .banner__copy {
    position: absolute;
    right: 76px;
    top: 88px;
    width: 560px;
    text-align: right;
  }
  .banner__title {
    margin: 0;
    font-size: 66px;
    line-height: 1;
    font-weight: 400;
    color: var(--title-gold);
    letter-spacing: 0.5px;
  }
  .banner__text {
    margin: 36px 0 0;
    font-size: 16px;
    line-height: 28px;
    color: var(--body-grey);
  }
</style>
</head>
<body>
  <section class="banner">
    <div class="banner__photo" role="img" aria-label="Photo of a sad teenage girl sitting apart while a group of classmates whisper and laugh by school lockers"></div>
    <div class="banner__copy">
      <h1 class="banner__title">Cyberbullying</h1>
      <p class="banner__text">Aliquam erat volutpat. Aliquam cursus sapien quis eros scelerisque,<br>sit amet interdum ligula ultrices non nulla sodales.</p>
    </div>
  </section>
</body>
</html>
```